MRT Property - Business Cards

Looking for a business card & general letterhead, signage etc design for our new logo.

Colours:
000a20
0056a2
00b5ef
0088ce
68cef2

Fonts:
Poppins
Karla

Please keep look and feel of new brand - example in the zip package I sent.

```html
<!DOCTYPE html>
<html lang="en">
<head>
<meta charset="utf-8">
<title>MRT Property – Business Cards</title>
<link rel="stylesheet" href="https://fonts.googleapis.com/css2?family=Poppins:wght@400;600;700&display=swap">
<style>
  :root {
    --navy: #0a0f1e;
    --brand-blue: #0056a2;
    --sky: #00b5ef;
    --mid-blue: #0088ce;
    --ice: #68cef2;
    --white: #ffffff;
    --stage: #e6e7ea;
  }
  * { box-sizing: border-box; margin: 0; padding: 0; }
  html, body { width: 1200px; height: 716px; overflow: hidden; }
  body {
    background: var(--stage);
    font-family: "Poppins", sans-serif;
    display: flex;
    align-items: center;
    justify-content: center;
    gap: 40px;
  }
  .card {
    position: relative;
    width: 540px;
    height: 310px;
    background: var(--navy);
    overflow: hidden;
  }
  .brand-decoration {
    position: absolute;
  }
  .card-front .brand-decoration {
    right: 0;
    bottom: 0;
    width: 230px;
    height: 190px;
    background: linear-gradient(100deg, var(--ice) 0%, var(--ice) 45%, var(--mid-blue) 60%, var(--sky) 100%);
    border-top-left-radius: 60px;
  }
  .card-back .brand-decoration {
    left: 0;
    top: 0;
    width: 230px;
    height: 250px;
    background: linear-gradient(160deg, var(--sky) 0%, var(--mid-blue) 45%, rgba(0, 136, 206, 0.35) 100%);
    border-bottom-right-radius: 180px;
  }
  .wordmark {
    position: absolute;
    font-weight: 700;
    color: var(--brand-blue);
    letter-spacing: 0.5px;
    white-space: nowrap;
  }
  .card-front .wordmark { left: 44px; top: 48px; font-size: 34px; }
  .card-back .wordmark { right: 34px; top: 70px; font-size: 28px; }

  .contact-block {
    position: absolute;
    right: 52px;
    top: 124px;
    text-align: right;
    color: var(--white);
  }
  .identity {
    position: relative;
    margin-bottom: 14px;
  }
  .identity::after {
    content: "";
    position: absolute;
    right: -16px;
    top: 4px;
    width: 6px;
    height: 42px;
    background: var(--brand-blue);
  }
  .person-name {
    font-weight: 700;
    font-size: 17px;
    color: var(--brand-blue);
    text-transform: uppercase;
    letter-spacing: 0.5px;
    line-height: 1.2;
  }
  .person-role { font-size: 12.5px; line-height: 1.3; }
  .address { font-size: 12.5px; line-height: 1.4; margin-bottom: 10px; }
  .contact-list { list-style: none; font-size: 12.5px; line-height: 1.55; }
  .contact-list li { display: flex; align-items: center; justify-content: flex-end; gap: 8px; }
  .contact-list svg { width: 12px; height: 12px; fill: none; stroke: var(--mid-blue); stroke-width: 2; }
</style>
</head>
<body>
  <section class="card card-front" aria-label="Business card front">
    <div class="wordmark">MRT Property</div>
    <div class="brand-decoration" role="img" aria-label="Large blue brand swoosh decoration"></div>
  </section>

  <section class="card card-back" aria-label="Business card back">
    <div class="brand-decoration" role="img" aria-label="Large blue brand swoosh decoration"></div>
    <div class="wordmark">MRT Property</div>
    <div class="contact-block">
      <div class="identity">
        <p class="person-name">Daniel Hart</p>
        <p class="person-role">Managing Director</p>
      </div>
      <p class="address">Your address, City<br>State, Zip 1234</p>
      <ul class="contact-list">
        <li>123 456 789
          <svg viewBox="0 0 24 24"><path d="M5 3h4l2 5-3 2a12 12 0 0 0 6 6l2-3 5 2v4a2 2 0 0 1-2 2A18 18 0 0 1 3 5a2 2 0 0 1 2-2z"/></svg>
        </li>
        <li>info@yourgmail.com
          <svg viewBox="0 0 24 24"><rect x="3" y="5" width="18" height="14" rx="1"/><path d="M3 6l9 7 9-7"/></svg>
        </li>
        <li>www.yourwebsite.com
          <svg viewBox="0 0 24 24"><circle cx="12" cy="12" r="9"/><path d="M3 12h18M12 3c3 3 3 15 0 18M12 3c-3 3-3 15 0 18"/></svg>
        </li>
      </ul>
    </div>
  </section>
</body>
</html>
```